I need a SEO-friendly Wordpress website (making sure to style H1, H2, H3, etc correctly) for a Hawaii-based law firm called Meridian Crest Legal Group. Comparable websites include https://brvlaw.example/ and https://www.lomrit.example/ for design reference. The current copy on the TarnAdvocate.example website can be used.

```html
<!DOCTYPE html>
<html lang="en">
<head>
<meta charset="utf-8">
<title>Meridian Crest Legal Group — Divorce and Personal Injury Lawyers</title>
<link rel="stylesheet" href="https://fonts.googleapis.com/css2?family=Lato:wght@400;700;900&display=swap">
<style>
:root{
  --brand-dark:#7a2a0c;
  --brand:#a4480f;
  --brand-deep:#6b1f08;
  --text:#3a3a3a;
  --text-soft:#555;
  --white:#fff;
  --footer:#2e2e2e;
  --footer-text:#b9b9b9;
  --footer-head:#ececec;
  --line:#e2e2e2;
}
*{box-sizing:border-box;margin:0;padding:0}
html,body{width:1200px;height:2706px;overflow:hidden}
body{font-family:'Lato',sans-serif;color:var(--text);background:var(--white);position:relative}
a{text-decoration:none;color:inherit}
ul{list-style:none}
.btn{display:inline-flex;align-items:center;justify-content:center;width:181px;height:47px;border-radius:24px;background:var(--brand);color:var(--white);font-weight:700;font-size:15px;letter-spacing:.3px;text-transform:uppercase}

/* header */
.site-header{position:relative;height:133px}
.brand{position:absolute;left:73px;top:42px}
.brand-name{font-size:25px;font-weight:900;color:var(--brand-dark);text-transform:uppercase;letter-spacing:-.2px}
.brand-tag{font-size:16px;font-weight:700;color:var(--brand);margin-top:6px}
.header-phone{position:absolute;right:73px;top:31px;font-size:18px;font-weight:700;color:var(--brand-dark);display:flex;align-items:center;gap:16px}
.main-nav{position:absolute;right:73px;top:84px;display:flex;gap:36px;font-size:14px;font-weight:700;color:#222;text-transform:uppercase}
.main-nav a{padding:2px 13px 7px;position:relative}
.main-nav a:last-child{padding-right:0}
.main-nav a.active{color:var(--brand)}
.main-nav a.active::after{content:"";position:absolute;left:0;right:0;bottom:-4px;height:3px;background:var(--brand)}

/* hero */
.hero{position:relative;height:526px;background:linear-gradient(100deg,#2a2420 0%,#4b3f36 40%,#6d5c50 70%,#8a7a6e 100%)}
.hero-copy{position:absolute;left:75px;top:130px;color:var(--white)}
.hero h1{font-size:41px;font-weight:900;line-height:44px;text-transform:uppercase}
.hero-sub{font-size:21px;margin-top:22px}
.hero-list{margin-top:10px}
.hero-list li{font-size:18px;display:flex;align-items:center;gap:17px;height:32px}
.hero .btn{margin-top:16px}
.hero-dots{position:absolute;left:75px;top:473px;display:flex;gap:9px}
.hero-dots span{width:10px;height:10px;border-radius:50%;background:var(--white)}
.hero-dots span:first-child{background:var(--brand)}

/* about */
.about{height:338px;text-align:center;padding-top:64px}
.section-title{font-size:29px;font-weight:700;text-transform:uppercase;color:var(--brand-dark)}
.about p{width:1010px;margin:18px auto 0;font-size:16px;line-height:26px;color:var(--text-soft)}
.about .btn{margin-top:34px}

/* practice */
.practice{height:541px;background:linear-gradient(90deg,#9a4110 0%,#853310 55%,#6b1f08 100%);padding-top:53px}
.practice .section-title{color:var(--white);text-align:center}
.practice-grid{position:absolute;left:75px;top:1113px;display:flex;gap:28px}
.practice-card{width:242px;height:364px;background:var(--white);text-align:center;position:relative}
.practice-photo{height:173px}
.practice-icon{position:absolute;left:87px;top:140px;width:68px;height:68px;border-radius:50%;background:var(--white);border:3px solid #ddd;display:flex;align-items:center;justify-content:center}
.practice-card h3{font-size:17px;font-weight:700;color:var(--brand);text-transform:uppercase;margin-top:50px;line-height:21px;padding:0 10px}
.practice-card p{font-size:15px;line-height:21px;color:var(--text-soft);margin-top:7px;padding:0 18px}

/* presence */
.presence{height:346px;background:linear-gradient(180deg,#3a4a62 0%,#2e3a4e 55%,#3d3c3a 100%);text-align:center;padding-top:54px;color:var(--white)}
.presence .section-title{color:var(--white)}
.presence p{width:910px;margin:18px auto 0;font-size:15px;line-height:28px}
.presence .btn{margin-top:28px}

/* team + blog */
.team-blog{position:relative;height:523px}
.team{position:absolute;left:75px;top:52px;width:490px}
.team .section-title,.blog .section-title{font-size:30px}
.attorney-list{display:flex;gap:32px;margin-top:40px}
.attorney{width:238px;text-align:center}
.attorney-photo{width:158px;height:158px;margin:0 auto;border-radius:50%;border:4px solid #d8d8d8;background:linear-gradient(160deg,#c9c4bf,#8f8780)}
.attorney h3{font-size:14px;font-weight:700;color:var(--brand);text-transform:uppercase;margin-top:26px}
.attorney p{font-size:14px;line-height:24px;color:#333;margin-top:4px}
.attorney .profile-link{display:block;font-size:15px;font-weight:700;color:var(--brand);margin-top:11px}
.divider{position:absolute;left:599px;top:60px;width:1px;height:388px;background:var(--line)}
.blog{position:absolute;left:640px;top:52px;width:490px}
.post{margin-top:20px}
.post + .post{margin-top:28px}
.post h3{font-size:17px;font-weight:700;color:var(--brand);text-transform:uppercase}
.post p{font-size:15px;line-height:26px;color:#444;margin-top:6px}
.post a{display:block;font-size:15px;color:var(--brand);margin-top:4px}

/* footer */
.site-footer{position:relative;height:299px;background:var(--footer);color:var(--footer-text)}
.footer-brand{position:absolute;left:73px;top:96px}
.footer-brand .name{font-size:25px;font-weight:900;color:#9a9a9a;line-height:27px;text-transform:uppercase}
.footer-brand .copy{font-size:13px;line-height:20px;margin-top:14px;padding-left:3px}
.social{display:flex;gap:18px;margin-top:18px;padding-left:3px}
.social span{width:18px;height:18px;border-radius:50%;background:#9a9a9a}
.footer-col{position:absolute;top:54px}
.footer-col h4{font-size:17px;font-weight:700;color:var(--footer-head);text-transform:uppercase;margin-bottom:14px}
.footer-col li{font-size:14px;height:32px}
.col-sitemap{left:376px}
.col-practice{left:593px}
.col-contact{left:901px}
.col-contact address{font-style:normal;font-size:14px;line-height:21px}
.contact-line{display:flex;align-items:center;gap:20px;font-size:14px;margin-top:10px}
</style>
</head>
<body>

<header class="site-header">
  <a class="brand" href="#">
    <div class="brand-name">Meridian Crest Legal Group</div>
    <div class="brand-tag">Divorce and Personal Injury Lawyers</div>
  </a>
  <div class="header-phone">
    <svg width="16" height="16" viewBox="0 0 24 24" aria-hidden="true"><path fill="#7a2a0c" d="M6.6 10.8a15.1 15.1 0 0 0 6.6 6.6l2.2-2.2c.3-.3.7-.4 1-.2 1.1.4 2.3.6 3.6.6.6 0 1 .4 1 1V20c0 .6-.4 1-1 1A17 17 0 0 1 3 4c0-.6.4-1 1-1h3.5c.6 0 1 .4 1 1 0 1.2.2 2.4.6 3.6.1.3 0 .7-.2 1z"/></svg>
    +1.808.555.0142
  </div>
  <nav class="main-nav">
    <a class="active" href="#">Home</a>
    <a href="#">Practice Areas</a>
    <a href="#">Attorneys</a>
    <a href="#">Blog</a>
    <a href="#">Contact Us</a>
  </nav>
</header>

<section class="hero">
  <div role="img" aria-label="Photo of lawyers meeting with a couple over documents at a desk" style="position:absolute;inset:0"></div>
  <div class="hero-copy">
    <h1>Welcome to<br>Meridian Crest Legal Group</h1>
    <p class="hero-sub">Over 70 years of combined practice, specializing in:</p>
    <ul class="hero-list">
      <li><svg width="16" height="16" viewBox="0 0 16 16" aria-hidden="true"><circle cx="8" cy="8" r="8" fill="#fff"/><path d="M4.5 8.2l2.3 2.3 4.7-4.8" stroke="#3a322c" stroke-width="2" fill="none"/></svg>Personal Injury</li>
      <li><svg width="16" height="16" viewBox="0 0 16 16" aria-hidden="true"><circle cx="8" cy="8" r="8" fill="#fff"/><path d="M4.5 8.2l2.3 2.3 4.7-4.8" stroke="#3a322c" stroke-width="2" fill="none"/></svg>Family &amp; Divorce</li>
      <li><svg width="16" height="16" viewBox="0 0 16 16" aria-hidden="true"><circle cx="8" cy="8" r="8" fill="#fff"/><path d="M4.5 8.2l2.3 2.3 4.7-4.8" stroke="#3a322c" stroke-width="2" fill="none"/></svg>Child Custody</li>
    </ul>
    <a class="btn" href="#">Read More</a>
  </div>
  <div class="hero-dots"><span></span><span></span><span></span><span></span></div>
</section>

<section class="about">
  <h2 class="section-title">About the Kona Lawyers of MCLG</h2>
  <p>The Halvorsen Group of Companies provides reporting issuers and private clients the following offerings – NRT Corporate Services and NRT Filing Services; KVL Financial Accounting and KVL Outsourced Chief Financial Officer Services. Clients can chose one or all of the service(s), but engaging more services together offers our clients the most synergies and cost savings.</p>
  <a class="btn" href="#">Read More</a>
</section>

<section class="practice">
  <h2 class="section-title">Areas of Practice</h2>
  <div class="practice-grid">
    <article class="practice-card">
      <div class="practice-photo" role="img" aria-label="Photo of a family meeting with a lawyer" style="background:linear-gradient(135deg,#e9dfd3,#9a8d80)"></div>
      <div class="practice-icon"><svg width="30" height="26" viewBox="0 0 30 26" aria-hidden="true"><g fill="#a4480f"><circle cx="15" cy="6" r="5"/><circle cx="6" cy="8" r="3.5"/><circle cx="24" cy="8" r="3.5"/><path d="M7 24c0-6 3.5-9 8-9s8 3 8 9z"/><path d="M0 22c0-5 2.5-7 6-7 1 0 2 .3 2.7.8C7 17.5 6 20 6 22z"/><path d="M30 22c0-5-2.5-7-6-7-1 0-2 .3-2.7.8 1.7 1.7 2.7 4.2 2.7 6.2z"/></g></svg></div>
      <h3>Family &amp; Divorce</h3>
      <p>Vestibulum ante ipsum primis in faucibus orci luctus et ultrices posuere..</p>
    </article>
    <article class="practice-card">
      <div class="practice-photo" role="img" aria-label="Photo of an injured wrist in a brace" style="background:linear-gradient(135deg,#3a4a6a,#c7a08f)"></div>
      <div class="practice-icon"><svg width="24" height="28" viewBox="0 0 24 28" aria-hidden="true"><g fill="#a4480f"><circle cx="12" cy="6" r="5.5"/><path d="M1 28v-6c0-5 4-8 11-8s11 3 11 8v6z"/></g><rect x="7" y="19" width="6" height="6" fill="#fff"/></svg></div>
      <h3>Personal Injury</h3>
      <p>Vestibulum ante ipsum primis in faucibus orci luctus et ultrices posuere..</p>
    </article>
    <article class="practice-card">
      <div class="practice-photo" role="img" aria-label="Photo of a smiling businessman in a meeting" style="background:linear-gradient(135deg,#d5d5d5,#4a4a4a)"></div>
      <div class="practice-icon"><svg width="30" height="26" viewBox="0 0 30 26" aria-hidden="true"><path d="M10 5V2h10v3" stroke="#a4480f" stroke-width="2.5" fill="none"/><rect x="1" y="5" width="28" height="20" rx="3" fill="#a4480f"/><rect x="8" y="5" width="2" height="20" fill="#fff"/><rect x="20" y="5" width="2" height="20" fill="#fff"/></svg></div>
      <h3>Corporate &amp;<br>Intellectual Property</h3>
      <p>Vestibulum ante ipsum primis in faucibus orci luctus et ultrices posuere..</p>
    </article>
    <article class="practice-card">
      <div class="practice-photo" role="img" aria-label="Photo of a hand holding a small model house at sunset" style="background:linear-gradient(180deg,#f0c07c,#d9853c 60%,#3a2a24)"></div>
      <div class="practice-icon"><svg width="30" height="26" viewBox="0 0 30 26" aria-hidden="true"><path d="M15 2L1 14h4v11h7v-7h6v7h7V14h4z" fill="#a4480f"/></svg></div>
      <h3>Real Estate</h3>
      <p>Vestibulum ante ipsum primis in faucibus orci luctus et ultrices posuere..</p>
    </article>
  </div>
</section>

<section class="presence" role="img" aria-label="Background photo of a coastal city skyline at dusk">
  <h2 class="section-title">Nationwide Law Firm Presence</h2>
  <p>Kailua Kona serves as the firm's West Coast headquarters for litigation and representation on behalf of individuals and corporations involved in a wide range of legal matters. The firm and its attorneys are licensed to practice and represent clients in Hawaii, California, Arizona, Texas, and Washington D.C.</p>
  <a class="btn" href="#">Read More</a>
</section>

<section class="team-blog">
  <div class="team">
    <h2 class="section-title">Attorneys</h2>
    <div class="attorney-list">
      <div class="attorney">
        <div class="attorney-photo" role="img" aria-label="Portrait of attorney Daniel Ortvale"></div>
        <h3>Daniel Ortvale, Esq.</h3>
        <p>Daniel Ortvale graduated from the Westbrook University College of Law, in 1972.</p>
        <a class="profile-link" href="#">View Full Profile</a>
      </div>
      <div class="attorney">
        <div class="attorney-photo" role="img" aria-label="Portrait of attorney Thomas Brennick"></div>
        <h3>Thomas Brennick, Esq</h3>
        <p>Thomas Brennick graduated from the Westbrook University College of Law, in 1971.</p>
        <a class="profile-link" href="#">View Full Profile</a>
      </div>
    </div>
  </div>
  <div class="divider"></div>
  <div class="blog">
    <h2 class="section-title">Blog Posts</h2>
    <article class="post">
      <h3>Top 10 Things to Do Before Filing for Divorce</h3>
      <p>No one gets married with the intention of things not working out, but it's an unfortunate fact that many marriages don't work out in the end. For those who are in troubled marriage, here are the Top 10 things you should do before filing for a divorce.</p>
      <a href="#">Continue Reading</a>
    </article>
    <article class="post">
      <h3>Top 15 Things to Do During Custody Battle</h3>
      <p>It's already tragic enough when two people who planned on spending their lives together no longer wish to see that dream through, but to compound the tragedy is when children [and their custody] get caught in the crossfire.</p>
      <a href="#">Continue Reading</a>
    </article>
  </div>
</section>

<footer class="site-footer">
  <div class="footer-brand">
    <div class="name">Meridian Crest<br>Legal Group</div>
    <p class="copy">Copyright © 2019. Company Name<br>All Right Reserved</p>
    <div class="social"><span></span><span></span><span></span><span></span><span></span></div>
  </div>
  <div class="footer-col col-sitemap">
    <h4>Site Map</h4>
    <ul><li>Home</li><li>Practice Areas</li><li>Attorneys</li><li>Blog</li><li>Contact Us</li></ul>
  </div>
  <div class="footer-col col-practice">
    <h4>Practice Areas</h4>
    <ul><li>Family &amp; Divorce</li><li>Personal Injury</li><li>Corporate &amp; Intellectual Property</li><li>Real Estate</li></ul>
  </div>
  <div class="footer-col col-contact">
    <h4>Contact Info</h4>
    <address>42-1180 Lanakila Way,<br>Suite 210 Kailua Kona,<br>Hawaii 96740</address>
    <div class="contact-line"><svg width="14" height="14" viewBox="0 0 24 24" aria-hidden="true"><path fill="#b9b9b9" d="M6.6 10.8a15.1 15.1 0 0 0 6.6 6.6l2.2-2.2c.3-.3.7-.4 1-.2 1.1.4 2.3.6 3.6.6.6 0 1 .4 1 1V20c0 .6-.4 1-1 1A17 17 0 0 1 3 4c0-.6.4-1 1-1h3.5c.6 0 1 .4 1 1 0 1.2.2 2.4.6 3.6.1.3 0 .7-.2 1z"/></svg>+1.808.555.0142</div>
    <div class="contact-line"><svg width="14" height="12" viewBox="0 0 14 12" aria-hidden="true"><rect width="14" height="12" rx="1" fill="#b9b9b9"/><path d="M1 1.5l6 4.5 6-4.5" stroke="#2e2e2e" stroke-width="1.4" fill="none"/></svg>clients@tarnadvocate.example</div>
  </div>
</footer>

</body>
</html>
```